Poster for our band

We need a logo and poster designing for us to send to the venues we are performing at. Our band is called "Brisk"
Can use different backgrounds to make poster look more Arty
We would like the poster to look contemporary, modern and unique. As many or as little pictures can be used that I will send.
We perform at Holiday Parks, Hotels etc so the Poster needs to look classy and sophisticated.Can be Portrait or Landscape. Poster could be Black and White or Colour
A very creative Logo
Could contain the following script somewhere on the poster.

Performing hits by- The Drifters Nine, Two Harbours, Lend Over, Gordon Pellworth, Barons of Teme, Rafters, Q7, Marble Owls and many more.

Poster needs our website address.
www.thebandbrisk.example.co.uk

Poster needs our Agent Name and number

Represented by- ORV - 01632 960418

Target Market(s)

Holiday Parks
Hotels
Nightclubs
Bars

Industry/Entity Type

Landscape

Colors
000000

Requirements
Must have
• Can be Portrait or Landscape. Poster could be Black and White or Colour
A very creative Logo

www.thebandbrisk.example.co.uk

Nice to have
• Cool, Contemopoary, Modern design
Photos can be cut out or changed in anyway to make us look great.

```html
<!DOCTYPE html>
<html lang="en">
<head>
<meta charset="utf-8">
<title>Brisk – The Band poster</title>
<link rel="stylesheet" href="https://fonts.googleapis.com/css2?family=Oswald:wght@700&family=Roboto+Condensed:wght@400&family=Roboto:wght@700&family=Share+Tech&display=swap">
<style>
  :root {
    --page: #ffffff;
    --photo-dark: #1c1c1c;
    --photo-mid: #5a5a5a;
    --photo-light: #a8a8a8;
    --logo-steel: #8c8c8c;
    --band-red: #e3161b;
    --strip-amber: rgba(196, 112, 20, 0.78);
    --strip-amber-edge: rgba(120, 70, 10, 0.7);
    --text-white: #ffffff;
    --web-yellow: #f2b51c;
  }
  * { margin: 0; padding: 0; box-sizing: border-box; }
  html, body {
    width: 1200px; height: 1000px; overflow: hidden;
    background: var(--page);
  }
  .canvas { position: relative; width: 1200px; height: 1000px; }
  .poster {
    position: absolute; left: 47px; top: 140px;
    width: 1113px; height: 742px; overflow: hidden;
  }
  .poster__photo { position: absolute; inset: 0; width: 100%; height: 100%; }
  .logo {
    position: absolute; left: 148px; top: 226px; width: 860px;
    font-family: "Oswald", sans-serif; font-weight: 700;
    font-size: 318px; line-height: 1; letter-spacing: 14px;
    color: var(--logo-steel); text-align: center;
  }
  .logo__tagline {
    position: absolute; right: 108px; top: 528px;
    font-family: "Roboto", sans-serif; font-weight: 700;
    font-size: 34px; line-height: 1; color: var(--band-red);
    white-space: nowrap;
  }
  .hits {
    position: absolute; left: 0; top: 577px; width: 100%; height: 88px;
    background: linear-gradient(90deg, var(--strip-amber-edge), var(--strip-amber) 20%, var(--strip-amber) 80%, var(--strip-amber-edge));
    font-family: "Roboto Condensed", sans-serif; color: var(--text-white);
    text-align: center; white-space: nowrap;
  }
  .hits__intro { position: absolute; top: 7px; width: 100%; font-size: 22px; }
  .hits__list { position: absolute; top: 49px; width: 100%; font-size: 21.5px; }
  .contact {
    position: absolute; font-family: "Share Tech", sans-serif;
    line-height: 1; white-space: nowrap;
  }
  .contact--web { left: 33px; top: 688px; font-size: 28px; color: var(--web-yellow); }
  .contact--agent { right: 38px; top: 686px; font-size: 32px; color: var(--text-white); letter-spacing: 0.5px; }
</style>
</head>
<body>
<div class="canvas">
  <section class="poster">
    <svg class="poster__photo" viewBox="0 0 1113 742" preserveAspectRatio="none" role="img" aria-label="Black and white photograph of the three band members posing against an old brick building with weeds in front">
      <defs>
        <linearGradient id="photoTone" x1="0" y1="0" x2="1" y2="1">
          <stop offset="0" stop-color="#1c1c1c"/>
          <stop offset="0.5" stop-color="#5a5a5a"/>
          <stop offset="0.8" stop-color="#a8a8a8"/>
          <stop offset="1" stop-color="#5a5a5a"/>
        </linearGradient>
      </defs>
      <rect width="1113" height="742" fill="url(#photoTone)"/>
    </svg>
    <h1 class="logo">BRISK</h1>
    <p class="logo__tagline">The Band</p>
    <div class="hits">
      <p class="hits__intro">Performing hits by -</p>
      <p class="hits__list">The Drifters Nine, Two Harbours, Lend Over, Gordon Pellworth, Barons of Teme, Rafters, Q7, Marble Owls and many more.</p>
    </div>
    <p class="contact contact--web">www.thebandbrisk.example.co.uk</p>
    <p class="contact contact--agent">Represented by- ORV - 01632 960418</p>
  </section>
</div>
</body>
</html>
```